Wine Label Design-Hollow Creek Vineyard

Hollow Creek Vineyard is in the Barossa Valley in South Australia. The Barossa is recognized as Australia's premier wine region, producing Australia's icon wines and some " new takes on traditional".
This family owned and operated vineyard grows some exceptionally high quality fruit. Most of the fruit is sold and used for some of Australia's most iconic wines. Small quantities are retained by the owners for some wines with very limited availability. (Wines were previously sold as Brackwell Vineyards Hollow Creek ( Shiraz, Cabernet etc).

The wines will in the future be labeled simply ‘Hollow Creek Vineyard’. The label will launch this new identity for the single family single vineyard and its high quality wines which are a true expression of the vineyard and derive from the Hollow Creek common to this ancient area (800-2000 million years old).
The label should reflect
• Single vineyard, family owned
• vines in very old rock & soils
• High quality & reliability
• Edgy but true, design based thinking (Please note:blue is generally seen as an unacceptable colour for a wine label?? Don’t ask me why)

The wines will be sold mostly direct in Australia ( ie not through retail stores), with limited export to Asia, Scandinavia and Canada.
There are three quality levels and price points in the portfolio
1. Entry level premium for everyday drinking for discriminating drinkers-approx AUD20
2. Super Premium-approx AUD30
3. Limited Release ultlra premium-AUD75-90?
We envisage three variations on the label but with an obvious & common design element. This design element should be able to be used for corporate identification and promotion
The paper stock will be waterproof and self adhesive. Our preference is for designs that engage the user by appealing to both sight and touch. It is preferred that textures be added eg embossing, high build varnish etc-rather than be a facet of the stock itself.
For information on statutory label requirements refer to www.vintnerregistry-example.com . In brief
o Front label need not show any mandatory information. However we would prefer Variety, Barossa Valley, Year and alcohol to be shown on the front label
o Back label should show all mandatories and allow for a bar code
Updates

Project Deadline Extended
Reason: I've had a problem with my wireless broadband account and reception has been intermittent to say the least to the extent that I switched off at the weekend. Just going downtown now for a 'polite discussion' with my service provider.

Project Deadline Extended
Reason: I have receiver insufficient designs of quality which we would consider. Too many designs have a "cut and paste" appearance - too few exhibit an original art/design element which truly identifies the product.

Gals & Guys

most of the designs submitted lack punch and originality and are totally unmemorable.
Please-get on Searcho or whatever enter "Wine Label Designs" and do some research b4 u waste your time and mine. Formulaic cut and paste will not win the day. That's not to say that cut and paste can't work-but it must have some originality, impact and command attention. Please surprise me.

Following on from a question from a designer about who is our competition and what we are looking for I sent the following 
"I don't think I can add anything new. Read the brief and comments again and research wine labels on the web. In 30 minutes you'll get a good idea of the creative edgy designs in the industry. There are a plethora of collections. Our competition-anyone with a label. In 2010 there were over 2400 "producers" in other words 2400 producers with at least one label. In fact there are over 25000 Australian wines and then the numerous imported wines.

Target Market(s)

$20 people who budget everyday but have graduated from drinking 'entry level' wines. These people will likely fit into Cat. (b) in the $30 wine

$30 (a) will not over-compromise on some everyday discretionary expenditure.(b) might buy for special occasions

$70-$90 Professional/successful people with high disposable/discretionary income not particularly worried about recession. wine geeks.

Industry/Entity Type

Retail

Requirements
Must have
• identifiable element across range of wines

```html
<!DOCTYPE html>
<html lang="en">
<head>
<meta charset="utf-8">
<title>Hollow Creek Vineyard – Front Label</title>
<link rel="stylesheet" href="https://fonts.googleapis.com/css2?family=EB+Garamond:wght@400&display=swap">
<style>
  :root {
    --backdrop: #e4e5e7;
    --paper-edge: #ffffff;
    --edge-line: #5a5a5a;
    --silver-light: #f2f2f2;
    --silver-mid: #c9c9c9;
    --silver-dark: #8f8f8f;
    --ink: #1c1c1c;
    --ornament-dark: #4a4a4a;
    --ornament-light: #b5b5b5;
  }
  * { margin: 0; padding: 0; box-sizing: border-box; }
  html, body {
    width: 1200px;
    height: 1200px;
    overflow: hidden;
    background: var(--backdrop);
  }
  .canvas {
    position: relative;
    width: 1200px;
    height: 1200px;
  }
  .front-label {
    position: absolute;
    left: 105px;
    top: 233px;
    width: 990px;
    height: 735px;
    filter: drop-shadow(0 6px 14px rgba(0,0,0,0.22));
  }
  .label-edge {
    position: absolute;
    inset: 0;
    width: 990px;
    height: 735px;
  }
  .label-content {
    position: absolute;
    inset: 0;
    display: flex;
    flex-direction: column;
    align-items: center;
    color: var(--ink);
    font-family: "EB Garamond", serif;
    font-weight: 400;
  }
  .winery-name {
    margin-top: 80px;
    font-family: "EB Garamond", serif;
    font-weight: 400;
    font-size: 76px;
    line-height: 1;
    letter-spacing: 1px;
  }
  .region {
    margin-top: 40px;
    font-size: 60px;
    line-height: 1;
  }
  .ornament {
    margin-top: 44px;
    width: 640px;
    height: 150px;
    border-radius: 50%;
    background: radial-gradient(ellipse at center, var(--ornament-dark) 0%, #7a7a7a 40%, rgba(181,181,181,0.6) 70%, rgba(181,181,181,0) 100%);
    opacity: 0.75;
  }
  .vintage {
    margin-top: 42px;
    font-size: 46px;
    line-height: 1;
  }
  .alcohol {
    position: absolute;
    right: 44px;
    bottom: 64px;
    font-size: 19px;
    line-height: 1;
  }
</style>
</head>
<body>
<main class="canvas">
  <section class="front-label" aria-label="Hollow Creek Vineyard front label">
    <svg class="label-edge" viewBox="0 0 990 735" aria-hidden="true">
      <defs>
        <linearGradient id="silver-sheen" x1="0" y1="0" x2="1" y2="0">
          <stop offset="0" stop-color="#8f8f8f"/>
          <stop offset="0.22" stop-color="#c9c9c9"/>
          <stop offset="0.5" stop-color="#f2f2f2"/>
          <stop offset="0.78" stop-color="#c9c9c9"/>
          <stop offset="1" stop-color="#8f8f8f"/>
        </linearGradient>
      </defs>
      <polygon class="torn-edge" fill="#ffffff" stroke="#5a5a5a" stroke-width="1.5"
        points="4,10 40,2 78,12 120,4 160,14 205,3 250,11 295,2 340,13 385,5 430,12 475,2 520,10 565,4 610,14 655,3 700,11 745,4 790,13 835,2 880,10 925,4 960,12 986,6
                980,45 988,90 978,135 987,180 979,225 988,270 980,315 986,360 978,405 987,450 980,495 988,540 979,585 986,630 978,675 985,730
                950,722 905,732 860,721 815,731 770,722 725,733 680,723 635,731 590,721 545,732 500,722 455,731 410,721 365,733 320,722 275,731 230,721 185,732 140,722 95,731 50,721 6,730
                12,690 3,645 13,600 4,555 12,510 2,465 11,420 4,375 13,330 3,285 12,240 4,195 13,150 2,105 11,60"/>
      <polygon class="silver-field" fill="url(#silver-sheen)"
        points="24,28 70,24 120,30 170,23 220,29 270,24 320,30 370,23 420,29 470,24 520,30 570,23 620,29 670,24 720,30 770,23 820,29 870,24 920,30 965,25
                962,80 968,140 961,200 967,260 960,320 968,380 961,440 967,500 960,560 967,620 962,680 966,708
                920,704 870,710 820,703 770,709 720,703 670,710 620,704 570,709 520,703 470,710 420,704 370,709 320,703 270,710 220,704 170,709 120,703 70,710 25,706
                29,650 22,590 28,530 23,470 29,410 22,350 28,290 23,230 29,170 22,110 28,60"/>
    </svg>
    <div class="label-content">
      <h1 class="winery-name">Hollow Creek Vineyard</h1>
      <p class="region">Barossa Valley</p>
      <div class="ornament" role="img" aria-label="Engraved symmetrical flourish ornament"></div>
      <p class="vintage">Vintage 2012</p>
      <p class="alcohol">13.5% Alc.Vol.</p>
    </div>
  </section>
</main>
</body>
</html>
```